New Business Card Design Project

I need a design for business cards, i am an electrical business called "Corvane Electrical and Communications" i need the cards to be double sided with the company logo on the back (attached) the front needs to say my company name, web site, email address, telephone number, and ABN number and electrical license number. I am open to different arrangements of the information but would like the background to be incorporating something electrical or something that looks smart. open to all additional ideas also.

The company colours are orange and grey see logo attached.

Business Name: Corvane Electrical and Communications
Website: corvaneelectricalandcomms.example.com.au
Email: brent@corvaneelectricalandcomms.example.com.au
Telephone(mobile): 0481209736
ABN: 71208349162
Lic No: 418273D

Target Market(s)

Business entities, Project Managers, Accounts, Clients

Industry/Entity Type

Electrician

Contact Information for Business Card

I need a design for business cards, i am an electrical business called "Corvane Electrical and Communications" i need the cards to be double sided with the company logo on the back (attached) the front needs to say my company name

Font styles to use
Serif
Sans Serif

Colors
f37122
5c5c5c

Requirements
Must have
• Must have the Logo on the back open to different ways of it being on the back but had in mind to keep it central but again open to other options
Nice to have
• A real modern cool background that is eye catching yet contemporary
Should not have
• No backgrounds of a light bulb or plug or anything like that

```html
<!DOCTYPE html>
<html lang="en">
<head>
<meta charset="utf-8">
<title>Corvane Electrical and Communications – Business Card</title>
<link rel="stylesheet" href="https://fonts.googleapis.com/css2?family=Questrial&family=Montserrat:wght@600;700&display=swap">
<style>
  :root {
    --bg: #e9e6e1;
    --card-white: #fafafa;
    --card-dark: #4f4f51;
    --card-dark-light: #616163;
    --grey: #5c5c5c;
    --grey-mid: #6e6e6e;
    --accent: #e6ad1f;
    --white: #ffffff;
  }
  * { box-sizing: border-box; margin: 0; padding: 0; }
  html, body {
    width: 1200px; height: 780px; overflow: hidden;
    background: var(--bg);
  }
  .canvas {
    width: 1200px; height: 780px;
    display: flex; align-items: center; justify-content: center; gap: 40px;
  }
  .card {
    position: relative;
    width: 540px; height: 310px;
    border-radius: 3px;
    overflow: hidden;
    box-shadow: 0 6px 18px rgba(0,0,0,.18);
  }

  /* ---------- Front ---------- */
  .card--front { background: var(--card-white); }
  .front__side-band {
    position: absolute; top: 0; right: 0;
    width: 16px; height: 258px; background: var(--accent);
  }
  .front__base-band {
    position: absolute; left: 0; bottom: 0;
    width: 100%; height: 16px; background: var(--grey-mid);
  }
  .front__social {
    position: absolute; top: 22px; right: 40px;
    display: flex; gap: 6px;
  }
  .front__social span {
    width: 18px; height: 18px; border-radius: 3px;
    background: #7aa8d8;
  }
  .front__person {
    position: absolute; top: 52px; right: 40px; text-align: right;
  }
  .person__name {
    font-family: "Montserrat", sans-serif; font-weight: 700;
    font-size: 20px; color: var(--grey); letter-spacing: .2px;
  }
  .person__role {
    font-family: "Questrial", sans-serif;
    font-size: 14px; color: var(--accent); margin-top: 1px;
  }
  .front__brand {
    position: absolute; left: 30px; top: 58px;
  }
  .brand__name {
    font-family: "Questrial", sans-serif;
    font-size: 64px; line-height: 1; color: var(--grey);
    letter-spacing: 2px;
  }
  .brand__tagline {
    font-family: "Montserrat", sans-serif; font-weight: 600;
    font-size: 13px; color: var(--accent); letter-spacing: 1.4px;
    margin-top: 6px; text-transform: uppercase;
  }
  .front__rule {
    position: absolute; left: 30px; right: 40px; top: 172px;
    height: 2px; background: var(--accent);
  }
  .front__registry {
    position: absolute; right: 40px; top: 184px; text-align: right;
    font-family: "Questrial", sans-serif; font-size: 13px; line-height: 1.5;
  }
  .registry__lic { color: var(--accent); }
  .registry__abn { color: var(--grey); }
  .front__contacts {
    position: absolute; left: 30px; bottom: 30px;
    list-style: none;
    font-family: "Questrial", sans-serif; font-size: 13px;
    color: var(--grey); line-height: 1.6;
  }
  .contacts__item { display: flex; align-items: center; gap: 8px; }
  .contacts__icon { width: 14px; height: 14px; flex: none; }

  /* ---------- Back ---------- */
  .card--back {
    background: radial-gradient(ellipse at 50% 45%, var(--card-dark-light), var(--card-dark) 75%);
    display: flex; flex-direction: column; align-items: center; justify-content: center;
  }
  .back__name {
    font-family: "Questrial", sans-serif;
    font-size: 74px; line-height: 1; color: var(--white); letter-spacing: 3px;
  }
  .back__tagline {
    font-family: "Montserrat", sans-serif; font-weight: 600;
    font-size: 14px; color: var(--accent); letter-spacing: 1.6px;
    margin-top: 12px; text-transform: uppercase;
  }
</style>
</head>
<body>
<main class="canvas">

  <section class="card card--front" aria-label="Business card front">
    <div class="front__side-band"></div>
    <div class="front__base-band"></div>
    <div class="front__social" aria-hidden="true"><span></span><span></span></div>

    <div class="front__person">
      <p class="person__name">Dale Harlow</p>
      <p class="person__role">Owner</p>
    </div>

    <div class="front__brand">
      <p class="brand__name">CORVANE</p>
      <p class="brand__tagline">Electrical &amp; Communications</p>
    </div>

    <div class="front__rule"></div>

    <div class="front__registry">
      <p class="registry__lic">Lic No: 418273D</p>
      <p class="registry__abn">ABN: 71208349162</p>
    </div>

    <ul class="front__contacts">
      <li class="contacts__item">
        <svg class="contacts__icon" viewBox="0 0 14 14" aria-hidden="true">
          <rect width="14" height="14" rx="2" fill="#e6ad1f"/>
          <rect x="4.5" y="2.5" width="5" height="9" rx="1" fill="none" stroke="#fff" stroke-width="1.2"/>
        </svg>
        <span>0481209736</span>
      </li>
      <li class="contacts__item">
        <svg class="contacts__icon" viewBox="0 0 14 14" aria-hidden="true">
          <rect width="14" height="14" rx="2" fill="#e6ad1f"/>
          <rect x="2.5" y="4" width="9" height="6.5" fill="none" stroke="#fff" stroke-width="1.2"/>
          <path d="M2.5 4 L7 8 L11.5 4" fill="none" stroke="#fff" stroke-width="1.2"/>
        </svg>
        <span>brent@corvaneelectricalandcomms.example.com.au</span>
      </li>
      <li class="contacts__item">
        <svg class="contacts__icon" viewBox="0 0 14 14" aria-hidden="true">
          <rect width="14" height="14" rx="2" fill="#e6ad1f"/>
          <circle cx="7" cy="7" r="4.3" fill="none" stroke="#fff" stroke-width="1.1"/>
          <path d="M2.7 7 H11.3 M7 2.7 C5 5 5 9 7 11.3 M7 2.7 C9 5 9 9 7 11.3" fill="none" stroke="#fff" stroke-width="1"/>
        </svg>
        <span>corvaneelectricalandcomms.example.com.au</span>
      </li>
    </ul>
  </section>

  <section class="card card--back" aria-label="Business card back">
    <p class="back__name">CORVANE</p>
    <p class="back__tagline">Electrical &amp; Communications</p>
  </section>

</main>
</body>
</html>
```